Letter and Envelope Design For Harborline Realty

Please design a letter and an envelope incorporating our logo (See Attached). We are also launched a business card contest. Since we want them to match, please feel free to submit a design for both the business card and also the letter design and envelope.

Requirements
Must have
• The envelope, the letter and the business cards must match somehow connecting the designs. We want them to have something that holds them together besides the logo.

```html
<!DOCTYPE html>
<html lang="en">
<head>
<meta charset="utf-8">
<title>Harborline Realty Stationery</title>
<link rel="stylesheet" href="https://fonts.googleapis.com/css2?family=Montserrat:wght@500;600&family=Source+Sans+3:wght@400;600;700&display=swap">
<style>
  :root {
    --navy: #14238a;
    --slate: #58595b;
    --charcoal: #3b3b3c;
    --paper: #fafafa;
    --ink: #6b6b6b;
    --backdrop: #e4e4e4;
  }
  * { margin: 0; padding: 0; box-sizing: border-box; }
  html, body { width: 1200px; height: 825px; overflow: hidden; }
  body {
    background: var(--backdrop);
    font-family: "Source Sans 3", sans-serif;
    position: relative;
  }
  .sheet { position: absolute; background: var(--paper); overflow: hidden; }

  /* brand lockup */
  .brand { position: absolute; display: flex; flex-direction: column; align-items: center; }
  .brand-dot { border: 2px solid var(--navy); border-radius: 50%; }
  .brand-name {
    font-family: "Montserrat", sans-serif; font-weight: 600; color: var(--navy);
    text-transform: uppercase; text-align: center; line-height: 1.25; letter-spacing: 0.12em;
  }
  .brand.on-dark .brand-dot { border-color: #fff; }
  .brand.on-dark .brand-name { color: #fff; }

  /* letterhead */
  .letter { left: 81px; top: 82px; width: 467px; height: 660px; }
  .letter .brand { left: 38px; top: 10px; width: 110px; }
  .letter .brand-dot { width: 38px; height: 38px; margin-bottom: 6px; }
  .letter .brand-name { font-size: 10px; }
  .contact-list { position: absolute; left: 339px; top: 43px; font-size: 7.6px; color: #444; line-height: 9.6px; list-style: none; }
  .contact-list li::before { content: ""; display: inline-block; width: 4px; height: 4px; border-radius: 50%; background: var(--navy); margin-right: 3px; vertical-align: middle; }
  .salutation { position: absolute; left: 38px; top: 134px; font-size: 11.2px; font-weight: 700; color: #444; }
  .body-copy { position: absolute; left: 38px; top: 162px; width: 392px; font-size: 9.6px; line-height: 12.2px; color: var(--ink); text-align: justify; }
  .body-copy p { margin-bottom: 12.4px; }
  .signature { position: absolute; left: 38px; top: 460px; width: 92px; height: 46px; background: linear-gradient(120deg, #f2f2f2, #dcdcdc); border-radius: 4px; }
  .footer-band { position: absolute; left: 0; bottom: 0; width: 100%; height: 22px; background: var(--slate); }
  .footer-info { position: absolute; left: 28px; top: 6px; font-size: 7px; color: #fff; white-space: nowrap; }
  .footer-info span { margin-right: 6px; }
  .web-tab { position: absolute; top: 0; }
  .web-tab text { font-family: "Source Sans 3", sans-serif; fill: #fff; letter-spacing: 0.06em; }

  /* business cards */
  .card-front { left: 650px; top: 269px; width: 198px; height: 113px; }
  .card-front .brand { left: 8px; top: 28px; width: 86px; }
  .card-front .brand-dot { width: 30px; height: 30px; margin-bottom: 4px; }
  .card-front .brand-name { font-size: 8px; }
  .card-divider { position: absolute; left: 99px; top: 28px; width: 1px; height: 52px; background: #ccc; }
  .card-person { position: absolute; left: 108px; top: 28px; font-size: 5.2px; color: #555; line-height: 6.6px; }
  .card-person .name { font-size: 7px; font-weight: 700; color: var(--navy); }
  .card-person .role { margin-bottom: 6px; }
  .card-person .addr { margin-top: 4px; }
  .card-front .footer-band { height: 13px; }
  .card-back { left: 867px; top: 269px; width: 198px; height: 113px; background: var(--charcoal); }
  .card-back .brand { left: 44px; top: 26px; width: 110px; }
  .card-back .brand-dot { width: 30px; height: 30px; margin-bottom: 5px; }
  .card-back .brand-name { font-size: 9px; }

  /* envelope */
  .envelope-flap { position: absolute; left: 585px; top: 442px; }
  .envelope { left: 585px; top: 510px; width: 536px; height: 232px; background: #fbfbfb; }
  .envelope .brand { left: 30px; top: 16px; width: 112px; }
  .envelope .brand-dot { width: 40px; height: 40px; margin-bottom: 6px; }
  .envelope .brand-name { font-size: 10px; }
  .envelope .footer-info { font-size: 7.6px; left: 36px; }
</style>
</head>
<body>

<section class="sheet letter" aria-label="Letterhead">
  <div class="brand"><div class="brand-dot"></div><div class="brand-name">Harborline<br>Realty</div></div>
  <ul class="contact-list">
    <li>555-214-0187</li>
    <li>hello@harborlinerealty.com</li>
    <li>www.harborlinerealty.com</li>
  </ul>
  <p class="salutation">Dear Mr. Carter,</p>
  <div class="body-copy">
    <p>Lorem Ipsum is simply dummy text of the printing and typesetting industry. Lorem Ipsum has been the industry's standard dummy text ever since the 1500s, when an unknown printer took a galley of type and scrambled it to make a type specimen book. It has survived not only five centuries, but also the leap into electronic typesetting, remaining essentially unchanged.</p>
    <p>The standard chunk of Lorem Ipsum used since the 1500s is reproduced below for those interested. Sections 1.10.32 and 1.10.33 from "de Finibus Bonorum et Malorum" by Cicero are also reproduced in their exact original form, accompanied by English versions from the 1914 translation by H. Rackham</p>
    <p>Lorem Ipsum is simply dummy text of the printing and typesetting industry. Lorem Ipsum has been the industry's standard dummy text ever since the 1500s, when an unknown printer took a galley of type and scrambled it to make a type specimen book. It has survived not only five centuries, but also the leap into electronic typesetting, remaining essentially unchanged. It was popularised in the</p>
    <p>Lorem Ipsum is simply dummy text of the printing and typesetting industry. Lorem Ipsum has been the industry's standard dummy text ever since the 1500s, when an unknown printer took a galley of type and scrambled it to make a type specimen book. It has survived not only five centuries, but also the leap into electronic typesetting, remaining essentially unchanged. It was popularised in the</p>
  </div>
  <div class="signature" role="img" aria-label="Handwritten signature"></div>
  <div class="footer-band">
    <div class="footer-info"><span>&#9742; 555-300-4412</span><span>&#9993; info@harborline.com</span><span>&#9679; Po. box 201, Street Name, City Name, 00000</span></div>
    <svg class="web-tab" style="left:315px" width="126" height="22" viewBox="0 0 126 22">
      <path d="M0 0 H126 L112 16 Q108 21 100 21 H26 Q18 21 14 16 Z" fill="#fff"/>
      <path d="M3 0 H123 L110 14 Q106 19 99 19 H27 Q20 19 16 14 Z" fill="var(--navy)"/>
      <text x="63" y="10.5" font-size="7.6" text-anchor="middle">www.harborline.com</text>
    </svg>
  </div>
</section>

<section class="sheet card-front" aria-label="Business card front">
  <div class="brand"><div class="brand-dot"></div><div class="brand-name">Harborline<br>Realty</div></div>
  <div class="card-divider"></div>
  <div class="card-person">
    <div class="name">DANA WHITFIELD</div>
    <div class="role">Manager</div>
    <div>&#9742; 555-214-0187</div>
    <div>&#9993; info@harborline.com</div>
    <div class="addr">Po. box 201, Street Name,<br>City Name, Zip Code - 00000</div>
  </div>
  <div class="footer-band">
    <svg class="web-tab" style="left:105px" width="82" height="13" viewBox="0 0 82 13">
      <path d="M0 0 H82 L74 9 Q71 12 66 12 H16 Q11 12 8 9 Z" fill="#fff"/>
      <path d="M2 0 H80 L73 8 Q70 11 65 11 H17 Q12 11 9 8 Z" fill="var(--navy)"/>
      <text x="41" y="7" font-size="5" text-anchor="middle">www.harborline.com</text>
    </svg>
  </div>
</section>

<section class="sheet card-back" aria-label="Business card back">
  <div class="brand on-dark"><div class="brand-dot"></div><div class="brand-name">Harborline<br>Realty</div></div>
</section>

<svg class="envelope-flap" width="536" height="69" viewBox="0 0 536 69" aria-hidden="true">
  <path d="M0 69 L12 42 Q20 32 40 28 L240 2 Q268 -2 296 2 L496 28 Q516 32 524 42 L536 69 Z" fill="var(--slate)"/>
</svg>
<section class="sheet envelope" aria-label="Envelope">
  <div class="brand"><div class="brand-dot"></div><div class="brand-name">Harborline<br>Realty</div></div>
  <div class="footer-band">
    <div class="footer-info">&#9679; Po. box 201, Street Name, City Name, Zip Code - 00000</div>
    <svg class="web-tab" style="left:362px" width="130" height="22" viewBox="0 0 130 22">
      <path d="M0 0 H130 L116 16 Q112 21 104 21 H26 Q18 21 14 16 Z" fill="#fff"/>
      <path d="M3 0 H127 L114 14 Q110 19 103 19 H27 Q20 19 16 14 Z" fill="var(--navy)"/>
      <text x="65" y="10.5" font-size="7.6" text-anchor="middle">www.harborline.com</text>
    </svg>
  </div>
</section>

</body>
</html>
```